German Headhunter/ HR Consultancy needs Business Cards Design

We need a business Card Design for our Company in Stuttgart. We are specialized as Headhunter/ HR Consultancy in Placement of specialist and managers in permanent employment. Please refer to our business logo.

```html
<!DOCTYPE html>
<html lang="en">
<head>
<meta charset="utf-8">
<title>Meridian Personalberatung – Business Cards</title>
<link rel="stylesheet" href="https://fonts.googleapis.com/css2?family=Montserrat:wght@400;500;600&display=swap">
<style>
  :root {
    --bg: #1b1b1d;
    --card: #222224;
    --blue: #3a56c6;
    --silver: #e6e6e8;
    --text: #d4d4d6;
    --muted: #9a9a9e;
  }
  * { box-sizing: border-box; margin: 0; padding: 0; }
  html, body { width: 1200px; height: 874px; overflow: hidden; }
  body {
    background: var(--bg);
    font-family: "Montserrat", sans-serif;
    position: relative;
  }
  .card {
    position: absolute;
    left: 300px;
    width: 600px;
    height: 343px;
    background: var(--card);
    border-radius: 18px;
    overflow: hidden;
    box-shadow: 0 14px 30px rgba(0,0,0,.55);
  }
  .card--front { top: 74px; }
  .card--back { top: 457px; }

  .brand { display: flex; align-items: center; gap: 14px; }
  .brand__mark { width: 34px; height: 34px; }
  .brand__name {
    font-weight: 600;
    line-height: 1.05;
    letter-spacing: .5px;
  }
  .brand__name span { display: block; }

  .card--front .brand {
    position: absolute; top: 108px; left: 0; right: 0; justify-content: center;
  }
  .card--front .brand__mark { background: var(--silver); }
  .card--front .brand__name { color: var(--silver); font-size: 36px; }
  .card--front .brand__name span + span { font-size: 16.5px; letter-spacing: 1.6px; }
  .tagline {
    position: absolute; top: 230px; left: 60px; right: 60px;
    text-align: center; color: var(--blue); font-size: 13px; line-height: 1.5;
  }

  .card--back .brand { position: absolute; top: 142px; left: 44px; gap: 10px; }
  .card--back .brand__mark { width: 26px; height: 26px; background: var(--blue); }
  .card--back .brand__name { color: var(--blue); font-size: 27px; }
  .card--back .brand__name span + span { font-size: 12.4px; letter-spacing: 1.2px; }

  .divider {
    position: absolute; left: 318px; top: 58px; width: 1.5px; height: 196px; background: var(--blue);
  }
  .contact { position: absolute; left: 340px; top: 56px; }
  .contact__name { color: var(--blue); font-size: 20px; font-weight: 600; letter-spacing: 1px; }
  .contact__role { color: var(--muted); font-size: 13px; margin-bottom: 14px; }
  .contact__address { color: var(--text); font-size: 13px; line-height: 1.35; margin-bottom: 8px; }
  .contact__list { list-style: none; color: var(--text); font-size: 13px; line-height: 1.38; }
  .contact__list li { display: flex; align-items: center; gap: 8px; }
  .contact__list svg { width: 11px; height: 11px; fill: var(--blue); flex: none; }
  .contact__list .no-icon { padding-left: 19px; }
  .band { position: absolute; left: 0; right: 0; bottom: 0; height: 14px; background: var(--blue); }
</style>
</head>
<body>
  <section class="card card--front" aria-label="Card front">
    <div class="brand">
      <div class="brand__mark"></div>
      <div class="brand__name"><span>MERIDIAN</span><span>PERSONALBERATUNG</span></div>
    </div>
    <p class="tagline">We are specialized as Headhunter/ HR Consultancy in Placement of specialist and managers in permanent employment.</p>
  </section>

  <section class="card card--back" aria-label="Card back">
    <div class="brand">
      <div class="brand__mark"></div>
      <div class="brand__name"><span>MERIDIAN</span><span>PERSONALBERATUNG</span></div>
    </div>
    <div class="divider"></div>
    <div class="contact">
      <p class="contact__name">JONAS BRENNER</p>
      <p class="contact__role">Founder &amp; CEO</p>
      <p class="contact__address">42 Lindenweg<br>Stuttgart 70173</p>
      <ul class="contact__list">
        <li><svg viewBox="0 0 24 24"><path d="M6.6 10.8a15 15 0 0 0 6.6 6.6l2.2-2.2c.3-.3.7-.4 1-.2 1.1.4 2.3.6 3.6.6.6 0 1 .4 1 1V20c0 .6-.4 1-1 1A17 17 0 0 1 3 4c0-.6.4-1 1-1h3.5c.6 0 1 .4 1 1 0 1.3.2 2.5.6 3.6.1.3 0 .7-.2 1z"/></svg>0711-555-0142</li>
        <li><svg viewBox="0 0 24 24"><path d="M7 1h10a2 2 0 0 1 2 2v18a2 2 0 0 1-2 2H7a2 2 0 0 1-2-2V3a2 2 0 0 1 2-2zm0 3v14h10V4z"/></svg>0711-555-0187</li>
        <li><svg viewBox="0 0 24 24"><path d="M6 2h12v6H6zM3 9h18a2 2 0 0 1 2 2v7h-4v4H5v-4H1v-7a2 2 0 0 1 2-2zm4 8v3h10v-3z"/></svg>0711-555-0193</li>
        <li><svg viewBox="0 0 24 24"><path d="M2 4h20v16H2zm2 2v.5l8 5 8-5V6z"/></svg>jonas@meridian-pb.de</li>
        <li><svg viewBox="0 0 24 24"><circle cx="12" cy="12" r="10"/></svg>www.meridian-pb.de</li>
      </ul>
    </div>
    <div class="band"></div>
  </section>
</body>
</html>
```